Business card design for a dynamic IT consulting company

We need a business card design for a young firm, specialized in the Telecommunications/Consulting industry. The name of the company is Quindor and Partners Business Consulting Ltd. (Short name: Quindor and Partnes)
Quindor = solve read reverse, so we aim to be uncomplicated and solution-oriented. The small pipe in our logo is also related to the word solve. So we need a new business card design, which is simple, eye catching and something non traditional (I would probably prefer a square shaped design rather than a rectangle, but open for suggestions). Attached our logo.

Target Market(s)

Usually our customers are Tier1 Telecoms providers (Q-Netra, Palorix, etc) and their executives.

Industry/Entity Type

Business

Contact Information for Business Card

Name: Bence Tolnavari
Email: b.tolnavari@quindor.hu
Web: www.quindor.hu
Mobile: +36 30 518 2769
Title: Managing Director

Optional:
Company name: Quindor and Partners Ltd.
Address: 1087 Budapest, Tolvenka str. 28/C, Hungary

Font styles to use
Other font styles liked:
• helveticaneue_medium, Prime Regular are used now.

Colors

Designer to choose colors to be used in the design.

Requirements
Must have
• I would like to have a 2 sided design.
Nice to have
• I thought if we make the logo a bit bigger (without the company name), that could go to the back with the company name below. I though, if the pipe in the logo is somehow touchable on the business card, would be nice and unique.

```html
<!DOCTYPE html>
<html lang="en">
<head>
<meta charset="utf-8">
<title>Quindor &amp; Partners – Business Card</title>
<link rel="stylesheet" href="https://fonts.googleapis.com/css2?family=Montserrat:wght@300;400;500;700&display=swap">
<style>
  :root {
    --stage: #d9d9d9;
    --card: #262626;
    --card-back: #1f1f1f;
    --ink: #e8e8e8;
    --ink-muted: #bdbdbd;
    --accent: #2a9fe0;
    --mark: #9a9a9a;
  }
  * { box-sizing: border-box; margin: 0; padding: 0; }
  html, body { width: 1200px; height: 900px; overflow: hidden; }
  body {
    background: var(--stage);
    font-family: "Montserrat", Arial, sans-serif;
    position: relative;
  }
  .card {
    position: absolute;
    left: 290px;
    width: 620px;
    height: 390px;
    border-radius: 4px;
    box-shadow: 0 10px 30px rgba(0,0,0,.25);
    overflow: hidden;
  }
  .card--back { top: 40px; background: var(--card-back); }
  .card--front { top: 470px; background: var(--card); }

  .back-brand {
    position: absolute;
    left: 0; right: 0; top: 50%;
    transform: translateY(-50%);
    display: flex;
    align-items: center;
    justify-content: center;
    gap: 18px;
  }
  .back-brand__square { width: 34px; height: 34px; background: var(--mark); }
  .back-brand__name {
    font-size: 44px;
    font-weight: 400;
    color: var(--mark);
    letter-spacing: .5px;
  }

  .front-brand {
    position: absolute;
    left: 40px; top: 40px;
    display: flex; align-items: center; gap: 12px;
  }
  .front-brand__square { width: 20px; height: 20px; background: var(--ink); }
  .front-brand__name { font-size: 26px; font-weight: 400; color: var(--ink); }

  .contact {
    position: absolute;
    left: 40px; top: 150px;
    color: var(--ink);
  }
  .contact__name {
    font-size: 26px; font-weight: 700; color: var(--accent);
    letter-spacing: .5px;
  }
  .contact__title { font-size: 18px; font-weight: 300; margin-top: 2px; }
  .contact__address { font-size: 17px; font-weight: 300; line-height: 1.4; margin-top: 16px; }
  .contact__list { list-style: none; margin-top: 16px; font-size: 17px; font-weight: 300; }
  .contact__list li { display: flex; align-items: center; gap: 12px; line-height: 1.55; }
  .contact__icon { width: 14px; height: 14px; flex: none; }

  .front-pattern {
    position: absolute;
    right: 0; top: 0;
    width: 260px; height: 100%;
    background: linear-gradient(90deg, rgba(38,38,38,0) 0%, #4a4a4a 40%, #8c8c8c 75%, #e6e6e6 100%);
  }
</style>
</head>
<body>
  <section class="card card--back" aria-label="Business card, back side">
    <div class="back-brand">
      <span class="back-brand__square"></span>
      <span class="back-brand__name">Quindor &amp; Partners</span>
    </div>
  </section>

  <section class="card card--front" aria-label="Business card, front side">
    <div class="front-brand">
      <span class="front-brand__square"></span>
      <span class="front-brand__name">Quindor &amp; Partners</span>
    </div>

    <div class="contact">
      <h1 class="contact__name">Bence Tolnavari</h1>
      <p class="contact__title">Managing Director</p>
      <p class="contact__address">1087 Budapest,<br>Tolvenka str. 28/C, Hungary</p>
      <ul class="contact__list">
        <li>
          <svg class="contact__icon" viewBox="0 0 24 24" aria-hidden="true"><path fill="#2a9fe0" d="M6.6 10.8a15 15 0 0 0 6.6 6.6l2.2-2.2a1 1 0 0 1 1-.25 11.4 11.4 0 0 0 3.6.57 1 1 0 0 1 1 1V20a1 1 0 0 1-1 1A17 17 0 0 1 3 4a1 1 0 0 1 1-1h3.5a1 1 0 0 1 1 1c0 1.25.2 2.45.57 3.57a1 1 0 0 1-.25 1z"/></svg>
          +36 30 518 2769
        </li>
        <li>
          <svg class="contact__icon" viewBox="0 0 24 24" aria-hidden="true"><rect x="2.5" y="5" width="19" height="14" rx="1.5" fill="none" stroke="#2a9fe0" stroke-width="2"/><path d="M3 6l9 7 9-7" fill="none" stroke="#2a9fe0" stroke-width="2"/></svg>
          b.tolnavari@quindor.hu
        </li>
        <li>
          <svg class="contact__icon" viewBox="0 0 24 24" aria-hidden="true"><g fill="none" stroke="#2a9fe0" stroke-width="1.8"><circle cx="12" cy="12" r="9.5"/><ellipse cx="12" cy="12" rx="4" ry="9.5"/><path d="M2.5 12h19M4 7h16M4 17h16"/></g></svg>
          www.quindor.hu
        </li>
      </ul>
    </div>

    <div class="front-pattern" role="img" aria-label="Decorative grid of grey raised squares fading from dark to white"></div>
  </section>
</body>
</html>
```